Keystonery Billboard - Financial Services Company (Investments, Tax Planning and Insurance)

Our new office has a billboard directly above the office building. We'd like something eye-catching with a strong Call to Action, with the main part of the billboard being under 7 words if possible. We'd like you to include a way to get ahold of us (either our website keystoneryllc.example or our phone number 302-418-2907. You may also include in small font something to indicate that we've been serving the area since 1980 (the DE area, the tri-state area, the Marlowe Hollow, etc.)

We offer financial planning, tax planning, and insurance, and we help our clients to focus on their goals and happiness by providing everything they need for lifelong wealth under one roof.

Our logos are attached, we use a triangle logo with green and gray. We use the tagline "discover lasting prosperity" but this does not need to be included.

Potential ideas we have seen from other financial companies-
- the concept that the driver spends more time looking at billboards than planning for their retirement
-something along the lines of "everything you need for your finances is in this building right here" planning, investments, taxes, insurance"
-don't spend your time worrying about retirement, let us help you plan for it
-are you working for your money, or is it working for you?
- retirement takes planning, we're here to help
- ready to retire? talk to us
- need investment advice?
- need help investing?
- crossing your fingers isn't a retirement plan. we can help.
- retiring soon? you need help.

Those are just general ideas, please feel free to be creative.

brand colors:
#00b585
#00b185
#000000
#ffffff
#6d6f75
#6d6f75
#6f7074
#021712
#052e24

```html
<!DOCTYPE html>
<html lang="en">
<head>
<meta charset="utf-8">
<title>Keystonery Billboard</title>
<link href="https://fonts.googleapis.com/css2?family=Montserrat:wght@600;700;800&family=Tinos:wght@700&display=swap" rel="stylesheet">
<style>
  :root{
    --page:#e4e5e6;
    --green-deep:#02432b;
    --green-mid:#1f7a52;
    --green-bright:#66f2a2;
    --brand-green:#00a36c;
    --site-green:#0a7a4a;
    --gray-text:#6d6f75;
    --band-light:#eeeeee;
    --white:#ffffff;
    --gold-1:#f6d34a;
    --gold-2:#c99a12;
  }
  *{box-sizing:border-box;margin:0;padding:0}
  html,body{width:1000px;height:1200px;overflow:hidden}
  body{background:var(--page);position:relative;font-family:"Montserrat",Arial,sans-serif}
  .billboard{position:absolute;left:40px;top:370px;width:920px;height:460px;background:var(--white);
    box-shadow:0 14px 30px rgba(0,0,0,.25);overflow:hidden}
  .hero{position:absolute;left:0;top:10px;width:920px;height:309px;
    background:linear-gradient(90deg,var(--green-deep) 0%,var(--green-mid) 45%,var(--green-bright) 88%)}
  .brand-box{position:absolute;right:0;top:0;width:324px;height:117px;background:var(--white);
    clip-path:polygon(0 0,100% 0,100% 100%,45px 100%)}
  .brand-name{position:absolute;right:20px;top:14px;display:flex;align-items:center;gap:8px;
    font-weight:600;font-size:29px;color:var(--brand-green);letter-spacing:-.5px;white-space:nowrap}
  .brand-mark{width:22px;height:22px;background:var(--brand-green)}
  .brand-tagline{position:absolute;right:20px;top:52px;font-size:6.5px;letter-spacing:2.4px;
    color:var(--gray-text);text-transform:uppercase;font-weight:600;white-space:nowrap}
  .brand-site{position:absolute;right:14px;top:72px;font-size:19px;font-weight:800;
    color:var(--site-green);white-space:nowrap;letter-spacing:-.2px}
  .brand-site span{font-weight:600;color:var(--gray-text)}
  .headline{position:absolute;left:44px;top:50px;color:var(--white);font-weight:800;line-height:1;letter-spacing:-1px}
  .headline .big{display:block;font-size:86px;height:86px}
  .headline .small{display:block;font-size:60px;margin-top:8px}
  .money-art{position:absolute;left:700px;top:105px;width:118px;height:194px;border-radius:30px;
    background:linear-gradient(135deg,var(--gold-1),var(--gold-2))}
  .services{position:absolute;left:0;top:319px;width:920px;height:73px;background:var(--band-light);
    display:flex;align-items:center;padding-left:40px;font-family:"Tinos","Times New Roman",serif;
    font-weight:700;font-size:40px;color:var(--gray-text)}
  .services .sep{width:3px;height:26px;background:#1f8a57;margin:0 20px}
  .contact{position:absolute;left:0;top:392px;width:920px;height:68px;background:var(--green-deep);
    display:flex;align-items:center;padding-left:40px;gap:8px;color:var(--white);font-weight:800;font-size:43px}
  .contact svg{width:40px;height:40px}
</style>
</head>
<body>
  <div class="billboard">
    <div class="hero">
      <h1 class="headline">
        <span class="big">WORRYING</span>
        <span class="big">ABOUT YOUR</span>
        <span class="small">MONEY? US TOO!</span>
      </h1>
      <div class="money-art" role="img" aria-label="Gold 3D dollar sign"></div>
    </div>
    <div class="brand-box">
      <div class="brand-name"><span class="brand-mark"></span>Keystonery</div>
      <div class="brand-tagline">discover lasting prosperity</div>
      <div class="brand-site">keystoneryllc<span>.example</span></div>
    </div>
    <div class="services">
      <span>Planning</span><span class="sep"></span>
      <span>Investments</span><span class="sep"></span>
      <span>Taxes</span><span class="sep"></span>
      <span>Insurance</span>
    </div>
    <div class="contact">
      <svg viewBox="0 0 40 40" aria-hidden="true">
        <circle cx="20" cy="20" r="19" fill="#ffffff"/>
        <path d="M13 11c1-1 2.5-1 3.3.2l2 3c.6 1 .3 2-.5 2.7l-1.3 1c.9 2.4 2.8 4.3 5.2 5.2l1-1.3c.7-.8 1.8-1.1 2.7-.5l3 2c1.2.8 1.2 2.3.2 3.3l-1.6 1.6c-1.5 1.5-4 1.4-6.5-.1-3.8-2.2-6.8-5.2-9-9-1.5-2.5-1.6-5-.1-6.5z" fill="#111"/>
        <path d="M22 10a8 8 0 0 1 8 8M22 14a4 4 0 0 1 4 4" stroke="#111" stroke-width="1.8" fill="none" stroke-linecap="round"/>
      </svg>
      <span>302-418-2907</span>
    </div>
  </div>
</body>
</html>
```